VELORA Brisbane Tiling Service

My name is Milos Brendt i need a business card for a new company. We are wall and floor tilers based in Brisbane, our company is Velorix Brisbane Tiling Service.
We would like a logo from our website used on our cards. Our website is www.velorix.com.au

I would like my Chatterbook and Postwave accounts on my card.

Industry/Entity Type

Business

Colors
0692cd
3176b5
33a6d7
85cae6

```html
<!DOCTYPE html>
<html lang="en">
<head>
<meta charset="utf-8">
<title>Velorix Brisbane Tiling Service – Business Cards</title>
<link rel="stylesheet" href="https://fonts.googleapis.com/css2?family=Lato:wght@400;700;900&display=swap">
<style>
  :root {
    --brand-blue: #0692cd;
    --brand-deep: #3176b5;
    --brand-mid: #33a6d7;
    --brand-light: #85cae6;
    --ink: #3a3a3a;
    --ink-soft: #666;
    --card-white: #fbfbfb;
    --tile-grey: #ececec;
    --backdrop: #d9d9d9;
  }
  * { box-sizing: border-box; margin: 0; padding: 0; }
  html, body { width: 1200px; height: 816px; overflow: hidden; }
  body {
    background: var(--backdrop);
    font-family: "Lato", Arial, sans-serif;
    color: var(--ink);
    position: relative;
  }
  .card {
    position: absolute;
    width: 560px;
    height: 320px;
    top: 248px;
    border-radius: 18px;
    background: var(--card-white);
    box-shadow: 0 6px 18px rgba(0,0,0,.18);
    overflow: hidden;
  }
  .card--back { left: 20px; }
  .card--front { left: 620px; }
  .card__pattern {
    position: absolute; inset: 0;
    background: radial-gradient(ellipse at 40% 40%, #ffffff 0%, var(--card-white) 45%, var(--tile-grey) 100%);
  }
  .brand {
    position: absolute;
    left: 0; right: 0;
    display: flex;
    justify-content: center;
    align-items: center;
    gap: 14px;
  }
  .brand__dot {
    border-radius: 50%;
    background: var(--brand-deep);
    flex: none;
  }
  .brand__name {
    color: var(--brand-deep);
    font-weight: 900;
    line-height: 1;
  }

  /* back card */
  .card--back .brand { top: 110px; }
  .card--back .brand__dot { width: 22px; height: 22px; }
  .card--back .brand__name { font-size: 56px; }
  .website {
    position: absolute; left: 0; right: 0; top: 226px;
    text-align: center;
    font-size: 16px; font-weight: 700; letter-spacing: 5px;
    color: var(--ink);
  }

  /* front card */
  .card--front .brand { top: 48px; }
  .card--front .brand__dot { width: 16px; height: 16px; }
  .card--front .brand__name { font-size: 40px; }

  .estimate { position: absolute; right: 34px; top: 140px; text-align: center; }
  .estimate__label {
    display: inline-block;
    background: var(--brand-deep);
    color: #fff;
    font-size: 13px; font-weight: 900;
    padding: 3px 8px; border-radius: 3px;
    letter-spacing: .3px;
  }
  .estimate__phone { color: var(--brand-deep); font-size: 27px; font-weight: 900; line-height: 1.05; }

  .divider { position: absolute; left: 0; top: 0; }

  .person { position: absolute; left: 34px; top: 176px; }
  .person__name { color: var(--brand-deep); font-size: 19px; font-weight: 900; }
  .person__role { color: var(--ink-soft); font-size: 13px; margin-top: 14px; }

  .contact { position: absolute; display: flex; align-items: center; gap: 10px; font-size: 15px; color: var(--ink); }
  .contact svg { flex: none; }
  .contact--phone { left: 36px; top: 250px; }
  .contact--mail { left: 36px; top: 280px; }
  .contact--social-post { left: 300px; top: 232px; font-size: 13.5px; }
  .contact--social-chat { left: 300px; top: 258px; font-size: 13.5px; }
  .social-dot { width: 12px; height: 12px; border-radius: 50%; background: var(--brand-deep); flex: none; }
</style>
</head>
<body>

  <section class="card card--back" aria-label="Business card back">
    <div class="card__pattern" role="img" aria-label="Faint grey tile pattern background"></div>
    <div class="brand">
      <span class="brand__dot"></span>
      <span class="brand__name">Velorix</span>
    </div>
    <p class="website">www.velorix.com.au</p>
  </section>

  <section class="card card--front" aria-label="Business card front">
    <div class="card__pattern" role="img" aria-label="Faint grey tile pattern background"></div>

    <div class="brand">
      <span class="brand__dot"></span>
      <span class="brand__name">Velorix</span>
    </div>

    <div class="estimate">
      <span class="estimate__label">CALL FOR A FREE ESTIMATE</span>
      <p class="estimate__phone">0412 650 318</p>
    </div>

    <svg class="divider" width="560" height="320" viewBox="0 0 560 320" aria-hidden="true">
      <polyline points="30,206 64,206 72,214 80,206 530,206" fill="none" stroke="#3176b5" stroke-width="2.2"/>
    </svg>

    <div class="person">
      <p class="person__name">Milos Brendt</p>
      <p class="person__role">Owner / Founder</p>
    </div>

    <div class="contact contact--phone">
      <svg width="14" height="20" viewBox="0 0 14 20" aria-hidden="true">
        <rect x="1" y="1" width="12" height="18" rx="2" fill="none" stroke="#3176b5" stroke-width="2"/>
        <line x1="5" y1="16" x2="9" y2="16" stroke="#3176b5" stroke-width="1.5"/>
      </svg>
      <span>07 3185 2947</span>
    </div>
    <div class="contact contact--mail">
      <svg width="18" height="14" viewBox="0 0 18 14" aria-hidden="true">
        <rect x="0" y="0" width="18" height="14" rx="1.5" fill="#3176b5"/>
        <polyline points="1,1 9,8 17,1" fill="none" stroke="#fff" stroke-width="1.5"/>
      </svg>
      <span>info@velorix.com.au</span>
    </div>

    <div class="contact contact--social-post">
      <span class="social-dot"></span>
      <span>postwave.com/Infovelorix</span>
    </div>
    <div class="contact contact--social-chat">
      <span class="social-dot"></span>
      <span>chatterbook.com/Velorix-Brisbane</span>
    </div>
  </section>

</body>
</html>
```